RWT Fittings Ltd Business Cards

We need a business card with our business logo. We provide window and door installations on high-rises in west coast British Colombia, Canada.

I would like my business information and details on one side of the card, and the other side the company name with logo

Target Market(s)

General Contractors

Industry/Entity Type

Construction

Contact Information for Business Card

one side i want my company name and logo in the dark theme logo that i provided

Requirements
Must have
• Marco Peltieri, 16045518293, RWTFittings@mailbox-demo.com, 1407-5194 Linden Row Burnaby BC, V5H 2K9, Owner & Manager

```html
<!DOCTYPE html>
<html lang="en">
<head>
<meta charset="utf-8">
<title>RWT Fittings Ltd – Business Card</title>
<link href="https://fonts.googleapis.com/css2?family=Open+Sans:wght@400;600;700&display=swap" rel="stylesheet">
<style>
  :root {
    --page-bg: #e8e4df;
    --card-dark: #161516;
    --card-mid: #242223;
    --teal: #2aa3c4;
    --teal-deep: #1b7f9c;
    --stone: #c9b9a6;
    --stone-muted: #a89a8a;
    --icon-grey: #8f8b86;
  }
  * { margin: 0; padding: 0; box-sizing: border-box; }
  html, body {
    width: 1200px;
    height: 1047px;
    overflow: hidden;
    background: var(--page-bg);
    font-family: "Open Sans", Arial, sans-serif;
  }
  .card {
    position: absolute;
    left: 100px;
    top: 251px;
    width: 1000px;
    height: 544px;
    border-radius: 22px;
    overflow: hidden;
    background: radial-gradient(ellipse at 55% 55%, var(--card-mid) 0%, var(--card-dark) 75%);
    box-shadow: 0 20px 50px rgba(0,0,0,0.25);
  }
  .brand {
    position: absolute;
    left: 40px;
    top: 70px;
    display: flex;
    align-items: center;
    gap: 18px;
  }
  .brand-mark {
    width: 56px;
    height: 56px;
    background: var(--stone-muted);
  }
  .brand-name {
    font-weight: 700;
    font-size: 46px;
    line-height: 1;
    color: var(--teal);
    letter-spacing: 0.5px;
  }
  .person {
    position: absolute;
    right: 31px;
    top: 56px;
    text-align: right;
    padding-right: 26px;
  }
  .person-name {
    font-weight: 700;
    font-size: 36px;
    line-height: 44px;
    color: var(--teal);
    letter-spacing: 0.5px;
  }
  .person-title {
    font-weight: 400;
    font-size: 25px;
    line-height: 34px;
    color: var(--stone);
  }
  .person-bar {
    position: absolute;
    right: 0;
    top: 2px;
    width: 16px;
    height: 68px;
    background: var(--teal);
  }
  .address {
    position: absolute;
    left: 38px;
    top: 244px;
    font-size: 25px;
    line-height: 34px;
    color: var(--stone);
  }
  .contacts {
    position: absolute;
    left: 38px;
    top: 412px;
    list-style: none;
  }
  .contacts li {
    display: flex;
    align-items: center;
    gap: 10px;
    font-size: 25px;
    line-height: 34px;
    color: var(--stone);
    white-space: nowrap;
  }
  .contacts svg { width: 20px; height: 20px; fill: var(--icon-grey); flex: none; }
  .contacts .globe { fill: none; stroke: var(--icon-grey); stroke-width: 2; }
  .building-art {
    position: absolute;
    left: 659px;
    top: 182px;
    width: 341px;
    height: 362px;
    background: linear-gradient(90deg, rgba(168,154,138,0.55) 0%, rgba(168,154,138,0.35) 45%, var(--teal-deep) 62%, var(--teal) 100%);
  }
</style>
</head>
<body>
  <main class="card">
    <div class="brand">
      <span class="brand-mark"></span>
      <span class="brand-name">RWT Fittings Ltd</span>
    </div>

    <div class="person">
      <p class="person-name">MARCO PELTIERI</p>
      <p class="person-title">Owner &amp; Manager</p>
      <span class="person-bar"></span>
    </div>

    <p class="address">1407-5194 Linden Row<br>Burnaby BC, V5H 2K9</p>

    <ul class="contacts">
      <li>
        <svg viewBox="0 0 24 24" aria-hidden="true"><path d="M6.6 10.8c1.4 2.8 3.8 5.1 6.6 6.6l2.2-2.2c.3-.3.7-.4 1-.2 1.1.4 2.3.6 3.6.6.6 0 1 .4 1 1V20c0 .6-.4 1-1 1C10.6 21 3 13.4 3 4c0-.6.4-1 1-1h3.5c.6 0 1 .4 1 1 0 1.3.2 2.5.6 3.6.1.3 0 .7-.2 1l-2.3 2.2z"/></svg>
        16045518293
      </li>
      <li>
        <svg viewBox="0 0 24 24" aria-hidden="true"><path d="M3 5h18v2l-9 6-9-6V5zm0 4.4l9 6 9-6V19H3V9.4z"/></svg>
        RWTFittings@mailbox-demo.com
      </li>
      <li>
        <svg class="globe" viewBox="0 0 24 24" aria-hidden="true"><circle cx="12" cy="12" r="9"/><ellipse cx="12" cy="12" rx="4" ry="9"/><path d="M3 12h18"/></svg>
        www.rwtfittings-demo.com
      </li>
    </ul>

    <div class="building-art" role="img" aria-label="Large decorative company emblem area"></div>
  </main>
</body>
</html>
```